Business Card Design

We are a commercial real estate brokerage in San Francisco, leasing office buildings downtown.
I would like a clean, elegant look. Simple but powerful .

Industry/Entity Type

Business

Contact Information for Business Card

Derek Holloway
lic# 07258143
415.555.0172
derek@velt-commercial.example
velt-commercial.example

```html
<!DOCTYPE html>
<html lang="en">
<head>
<meta charset="utf-8">
<title>Velt Commercial — Business Card</title>
<link href="https://fonts.googleapis.com/css2?family=PT+Sans:wght@400;700&display=swap" rel="stylesheet">
<style>
  :root {
    --backdrop: #ece8df;
    --card: #ffffff;
    --slate: #7688a8;
    --slate-text: #7586a6;
    --ink: #4a4d55;
    --divider: #55585f;
    --mark: #8a8d93;
    --skyline-top: #f1f2f4;
    --skyline-bottom: #e4e6ea;
  }
  * { margin: 0; padding: 0; box-sizing: border-box; }
  html, body {
    width: 1200px;
    height: 510px;
    overflow: hidden;
    background: var(--backdrop);
    font-family: "PT Sans", Arial, sans-serif;
  }
  .business-card {
    position: absolute;
    left: 224px;
    top: 34px;
    width: 752px;
    height: 441px;
    background: var(--card);
    border-radius: 20px;
    overflow: hidden;
  }
  .skyline {
    position: absolute;
    left: 374px;
    top: 104px;
    width: 378px;
    height: 243px;
    background: linear-gradient(180deg, var(--skyline-top), var(--skyline-bottom));
  }
  .brand {
    position: absolute;
    left: 82px;
    top: 60px;
    display: flex;
    align-items: center;
  }
  .brand-square {
    width: 72px;
    height: 72px;
    background: var(--mark);
  }
  .brand-divider {
    width: 2px;
    height: 80px;
    background: var(--divider);
    margin: 0 12px 0 14px;
  }
  .brand-name {
    color: var(--slate);
    font-weight: 700;
    line-height: 1;
    text-transform: uppercase;
  }
  .brand-name .primary { display: block; font-size: 50px; letter-spacing: 1px; }
  .brand-name .secondary { display: block; font-size: 25px; margin-top: 4px; letter-spacing: 0.5px; }
  .contact-list {
    position: absolute;
    left: 38px;
    top: 196px;
    list-style: none;
    color: var(--ink);
    font-size: 17px;
  }
  .contact-list li {
    display: flex;
    align-items: center;
    height: 29px;
  }
  .contact-icon {
    width: 14px;
    height: 14px;
    background: var(--slate);
    color: #fff;
    font-size: 11px;
    font-weight: 700;
    line-height: 14px;
    text-align: center;
    margin-right: 7px;
  }
  .footer-band {
    position: absolute;
    left: 0;
    top: 347px;
    width: 100%;
    height: 94px;
    background: var(--slate);
  }
  .agent-name {
    position: absolute;
    right: 52px;
    top: 310px;
    color: var(--slate-text);
    font-size: 31px;
    text-transform: uppercase;
    letter-spacing: 0.5px;
    line-height: 1;
  }
</style>
</head>
<body>
  <div class="business-card">
    <div class="skyline" role="img" aria-label="Faint illustration of downtown office towers"></div>

    <div class="brand">
      <div class="brand-square"></div>
      <div class="brand-divider"></div>
      <div class="brand-name">
        <span class="primary">Velt</span>
        <span class="secondary">Commercial</span>
      </div>
    </div>

    <ul class="contact-list">
      <li><span class="contact-icon"></span>lic# 07258143</li>
      <li><span class="contact-icon">m</span>415.555.0172</li>
      <li><span class="contact-icon">e</span>derek@velt-commercial.example</li>
      <li><span class="contact-icon">w</span>velt-commercial.example</li>
    </ul>

    <div class="footer-band"></div>
    <div class="agent-name">Derek Holloway</div>
  </div>
</body>
</html>
```